Redesign of business card for Cedar Ridge Mechanical

We are looking for a new design for our business cards for Cedar Ridge Mechanical. We are a plumbing & HVAC construction company, operating on the West Coast of Canada and USA. Logo attached.
Industry/Entity Type
Construction - Plumbing & HVAC
Contact Information for Business Card
Name, address, phone numbers, email, website address
Look and feel
Each slider illustrates characteristics of the customer's brand and the style your logo design should communicate.

```html
<!DOCTYPE html>
<html lang="en">
<head>
<meta charset="utf-8">
<title>Cedar Ridge Mechanical – Business Card</title>
<link href="https://fonts.googleapis.com/css2?family=Poppins:wght@300;400;700&display=swap" rel="stylesheet">
<style>
  :root {
    --canvas-bg: #232323;
    --card-bg: #1d1d20;
    --card-edge: #2a2a2e;
    --ink: #ffffff;
    --ink-soft: #e6e6e6;
    --back-ink: #2e2e33;
  }
  * { box-sizing: border-box; margin: 0; padding: 0; }
  html, body {
    width: 1200px; height: 780px; overflow: hidden;
    background: var(--canvas-bg);
    font-family: "Poppins", sans-serif;
  }
  .canvas {
    position: relative; width: 1200px; height: 780px;
    display: flex; align-items: center; justify-content: center; gap: 40px;
  }
  .card {
    position: relative; width: 525px; height: 300px;
    background: var(--card-bg);
    border: 1px solid var(--card-edge);
    overflow: hidden;
  }
  .card-front .light-band {
    position: absolute; left: -60px; right: -60px; top: 70px; height: 150px;
    background: linear-gradient(180deg, rgba(0,0,0,0) 0%, rgba(255,255,255,0.05) 45%, rgba(0,0,0,0.35) 100%);
  }
  .front-content {
    position: relative; height: 100%;
    display: flex; flex-direction: column; align-items: center; justify-content: center;
    color: var(--ink); text-align: center;
  }
  .brand-name {
    display: flex; align-items: center; gap: 8px;
    font-weight: 400; font-size: 15px; letter-spacing: 1.5px; text-transform: uppercase;
    margin-bottom: 16px;
  }
  .brand-mark { width: 12px; height: 12px; border: 2px solid var(--ink); }
  .person-name { font-size: 24px; line-height: 1.1; }
  .person-name .first { font-weight: 700; }
  .person-name .last { font-weight: 300; }
  .person-role { font-size: 12px; font-weight: 400; margin-top: 2px; margin-bottom: 10px; }
  .contact-icons { display: flex; gap: 5px; margin-bottom: 6px; }
  .contact-icons span { width: 12px; height: 12px; border-radius: 50%; background: var(--ink); }
  .contact-lines { font-size: 12px; font-weight: 300; line-height: 1.45; color: var(--ink-soft); }
  .address { margin-top: 8px; display: flex; flex-direction: column; align-items: center; gap: 4px; font-size: 12px; font-weight: 300; color: var(--ink-soft); }
  .pin { width: 13px; height: 13px; }
  .card-back { display: flex; align-items: center; justify-content: center; }
  .back-name {
    font-weight: 700; font-size: 30px; letter-spacing: 2px; text-transform: uppercase;
    color: var(--back-ink);
  }
</style>
</head>
<body>
<main class="canvas">
  <section class="card card-front">
    <div class="light-band"></div>
    <div class="front-content">
      <div class="brand-name"><span class="brand-mark"></span>Cedar Ridge Mechanical</div>
      <p class="person-name"><span class="first">Maren</span> <span class="last">Kowal</span></p>
      <p class="person-role">Founder &amp; CEO</p>
      <div class="contact-icons"><span></span><span></span><span></span></div>
      <div class="contact-lines">
        <p>(604) 555-0182</p>
        <p>info@cedarridgemech.com</p>
        <p>www.cedarridgemech.com</p>
      </div>
      <div class="address">
        <svg class="pin" viewBox="0 0 24 24" aria-hidden="true">
          <circle cx="12" cy="12" r="12" fill="#fff"/>
          <path d="M12 5a4.5 4.5 0 0 0-4.5 4.5c0 3.4 4.5 8.5 4.5 8.5s4.5-5.1 4.5-8.5A4.5 4.5 0 0 0 12 5zm0 6.3a1.8 1.8 0 1 1 0-3.6 1.8 1.8 0 0 1 0 3.6z" fill="#1d1d20"/>
        </svg>
        <p>48 Alder Bend Road, Nanaimo, BC V9R 2K4</p>
      </div>
    </div>
  </section>
  <section class="card card-back">
    <p class="back-name">Cedar Ridge Mechanical</p>
  </section>
</main>
</body>
</html>
```